Young Architect Bussiness Card

English is not my first language (spanish is).
Need a bussiness card design for my best friend who is about to graduate from college, Licentiate degree in architecture, so she needs business cards to start networking, currently she has no porfolio, web page or plazared. so she is relying on her cel phone and correovela, but should leave space for one of them (plazared)

Design for business card should be modern, maybe something with construction blue prints patern or 3D modelling.

Name: Mariela Otárola Bonilla
Licentiate in Arquitecture
Cel: (506) XXX-4827
email: marielaXXX@correovela.com

Services, although im not sure if it has to be there or not:
Anteproyectos / Proposal design
Inspecciones / Site Inspections
Modelado 3D / 3D modelling
Planos Constructivos / Construction Blue Prints
Presupuestos / Budgets

Design should be in spanish

Industry/Entity Type

Architect

Contact Information for Business Card

Name: Mariela Otárola, Arquitecto
Associtation code : XXXX
Phone: (506) XXXX-XXXX
Email: xxx@correovela.com
Plazared: xxxx

Requirements
Must have
• Design for business card should be modern, maybe something with construction blue prints patern or 3D modelling.
Nice to have
• Something like a transition from 2D to 3D.

```html
<!DOCTYPE html>
<html lang="es">
<head>
<meta charset="utf-8">
<title>Mariela Otárola Bonilla — Tarjeta de presentación</title>
<link href="https://fonts.googleapis.com/css2?family=Lato:wght@400;700;900&display=swap" rel="stylesheet">
<style>
  :root {
    --stage: #2b2b2b;
    --card-white: #ffffff;
    --brand-yellow: #f8ec2e;
    --accent-yellow: #f4d511;
    --cube-yellow: #f9e43a;
    --cube-yellow-soft: rgba(249, 228, 58, 0.55);
    --cube-yellow-clear: rgba(249, 228, 58, 0);
    --cube-dark: #1d1d1d;
    --cube-dark-soft: rgba(29, 29, 29, 0.6);
    --cube-dark-clear: rgba(29, 29, 29, 0);
    --ink: #151515;
  }
  * { margin: 0; padding: 0; box-sizing: border-box; }
  html, body {
    width: 1200px; height: 880px; overflow: hidden;
    background: var(--stage);
    font-family: "Lato", sans-serif;
  }
  .canvas {
    position: relative; width: 1200px; height: 880px;
    display: flex; flex-direction: column; align-items: center; justify-content: center;
    gap: 40px;
  }
  .card {
    position: relative; width: 640px; height: 366px;
    border-radius: 18px; overflow: hidden;
  }
  .card--front { background: var(--card-white); }
  .card--back { background: var(--brand-yellow); }

  .cube-art {
    position: absolute; top: 0; right: 0;
  }
  .cube-art--yellow {
    width: 380px; height: 300px;
    background: radial-gradient(closest-side at 60% 42%,
      var(--cube-yellow) 0%, var(--cube-yellow-soft) 60%, var(--cube-yellow-clear) 100%);
  }
  .cube-art--dark {
    top: -20px; right: -20px;
    width: 440px; height: 340px;
    background: radial-gradient(closest-side at 55% 50%,
      var(--cube-dark) 0%, var(--cube-dark-soft) 58%, var(--cube-dark-clear) 100%);
  }

  .identity { position: absolute; left: 46px; top: 128px; }
  .identity__name {
    color: var(--accent-yellow); font-weight: 400; font-size: 22px;
    letter-spacing: 0.5px; text-transform: uppercase;
  }
  .identity__title { color: var(--ink); font-size: 16px; margin-top: 4px; }

  .contact { position: absolute; left: 46px; bottom: 40px; font-size: 16px; line-height: 1.35; color: var(--ink); }
  .contact__label { color: var(--accent-yellow); }

  .services { position: absolute; left: 46px; bottom: 36px; color: var(--ink); }
  .services__heading { font-weight: 900; font-size: 18px; letter-spacing: 0.2px; margin-bottom: 8px; }
  .services__list { list-style: none; font-size: 15.5px; line-height: 1.3; }
</style>
</head>
<body>
  <main class="canvas">
    <section class="card card--front" aria-label="Frente de la tarjeta">
      <div class="cube-art cube-art--yellow" role="img" aria-label="Ilustración 3D de cubos amarillos que se dispersan, transición de 2D a modelado 3D"></div>
      <div class="identity">
        <h1 class="identity__name">Mariela Otárola Bonilla</h1>
        <p class="identity__title">Licentiate in Arquitecture</p>
      </div>
      <div class="contact">
        <p><span class="contact__label">Cell:</span> (506) XXX-4827</p>
        <p><span class="contact__label">Email:</span> marielaXXX@correovela.com</p>
      </div>
    </section>

    <section class="card card--back" aria-label="Reverso de la tarjeta">
      <div class="cube-art cube-art--dark" role="img" aria-label="Ilustración 3D de cubos negros que se dispersan, modelado 3D arquitectónico"></div>
      <div class="services">
        <h2 class="services__heading">SERVICES</h2>
        <ul class="services__list">
          <li>Anteproyectos / Proposal design</li>
          <li>Inspecciones / Site Inspections</li>
          <li>Modelado 3D / 3D modelling</li>
          <li>Planos Constructivos / Construction Blue Prints</li>
          <li>Presupuestos / Budgets</li>
        </ul>
      </div>
    </section>
  </main>
</body>
</html>
```